New Business card design to reflect rebrand

I would like a business card design with a good base colour for our new logo and also a placeholder for a profile pic of the card holder. the design needs to be editable to the point that we can easily change the picture of the person and use that design for printmerlo etc. we are looking at a metalic finish business card so will need a good base colour to bring out the finish.

Target Market(s)

prospective customers

Industry/Entity Type

Business

Contact Information for Business Card

I would like one editable design that we can change the name of the card holder and profile picture. The design need to be in a format that be send to printmerlo etc.

Our address is Fenwick Lodge, Copse Lane, Ashcombe Vale, GU14 3TP Tel no. 01483 556172

Requirements
Must have
• place holder for a profile pic for the card holder. in AI or preferably PSD format

```html
<!DOCTYPE html>
<html lang="en">
<head>
<meta charset="utf-8">
<title>Northvale Workplace Services – Business Card</title>
<link rel="stylesheet" href="https://fonts.googleapis.com/css2?family=Open+Sans:wght@400;600;700&display=swap">
<style>
  :root {
    --page-bg: #ecebe8;
    --navy: #3d5068;
    --navy-dark: #2f3f54;
    --navy-light: #4d627d;
    --orange: #e8681a;
    --orange-light: #f08a3c;
    --paper: #ffffff;
    --paper-shade: #e9e9e9;
    --text-light: #ffffff;
    --photo-tone: #9a9a9a;
  }
  * { margin: 0; padding: 0; box-sizing: border-box; }
  html, body {
    width: 1200px; height: 843px; overflow: hidden;
    background: var(--page-bg);
    font-family: "Open Sans", Arial, sans-serif;
  }
  .canvas { position: relative; width: 1200px; height: 843px; }
  .card {
    position: absolute; left: 300px;
    width: 600px; height: 343px;
    overflow: hidden;
    box-shadow: 0 6px 18px rgba(0,0,0,.18);
  }
  .brand {
    display: flex; align-items: center; gap: 10px;
    font-weight: 700; letter-spacing: .5px; white-space: nowrap;
  }
  .brand-mark { flex: none; background: var(--orange); }

  /* Back of card */
  .card-back {
    top: 48px;
    background: linear-gradient(135deg, var(--navy-light), var(--navy) 55%, var(--navy-dark));
    display: flex; flex-direction: column; align-items: center; justify-content: center;
    gap: 28px;
  }
  .card-back .brand { font-size: 28px; color: var(--text-light); }
  .card-back .brand-mark { width: 18px; height: 18px; }
  .web-address { color: var(--text-light); font-size: 13px; letter-spacing: 4px; }

  /* Front of card */
  .card-front {
    top: 452px;
    background: linear-gradient(180deg, var(--paper) 0%, var(--paper-shade) 100%);
  }
  .card-front .brand {
    position: absolute; left: 96px; top: 58px;
    font-size: 22px; color: var(--navy);
  }
  .card-front .brand-mark { width: 13px; height: 13px; }
  .name-band {
    position: absolute; left: 0; top: 150px; width: 100%; height: 56px;
    background: linear-gradient(90deg, var(--orange) 0%, var(--orange-light) 45%, var(--orange) 100%);
  }
  .holder { position: absolute; left: 28px; top: 156px; color: var(--text-light); }
  .holder-name { font-size: 20px; font-weight: 700; line-height: 1.2; }
  .holder-role { font-size: 14px; line-height: 1.3; }
  .profile-photo {
    position: absolute; left: 448px; top: 104px; width: 124px; height: 102px;
    background: linear-gradient(180deg, #b5b5b5, var(--photo-tone));
  }
  .info-band {
    position: absolute; left: 0; top: 206px; width: 100%; bottom: 0;
    background: linear-gradient(135deg, var(--navy-light), var(--navy) 60%, var(--navy-dark));
    border-top: 2px solid #c9d0d9;
    color: var(--text-light);
  }
  .phone {
    position: absolute; left: 0; right: 0; top: 26px;
    display: flex; align-items: center; justify-content: center; gap: 8px; font-size: 15px;
  }
  .phone svg { width: 14px; height: 14px; }
  .address {
    position: absolute; left: 0; right: 0; top: 74px; text-align: center;
    font-size: 15px; letter-spacing: .3px;
  }
</style>
</head>
<body>
<main class="canvas">
  <section class="card card-back" aria-label="Card back">
    <div class="brand"><span class="brand-mark"></span>Northvale Workplace Services</div>
    <p class="web-address">www.northvalews.co.uk</p>
  </section>

  <section class="card card-front" aria-label="Card front">
    <div class="brand"><span class="brand-mark"></span>Northvale Workplace Services</div>
    <div class="name-band"></div>
    <div class="holder">
      <p class="holder-name">Daniel Hart</p>
      <p class="holder-role">CEO/Founder</p>
    </div>
    <div class="profile-photo" role="img" aria-label="Profile photo placeholder for the card holder"></div>
    <div class="info-band">
      <p class="phone">
        <svg viewBox="0 0 24 24" aria-hidden="true"><path fill="#e8681a" d="M6.6 10.8a15.1 15.1 0 0 0 6.6 6.6l2.2-2.2c.3-.3.7-.4 1-.2 1.1.4 2.3.6 3.6.6.6 0 1 .4 1 1V20c0 .6-.4 1-1 1A17 17 0 0 1 3 4c0-.6.4-1 1-1h3.5c.6 0 1 .4 1 1 0 1.2.2 2.4.6 3.6.1.3 0 .7-.2 1z"/></svg>
        01483 556172
      </p>
      <p class="address">Fenwick Lodge, Copse Lane, Ashcombe Vale, GU14 3TP</p>
    </div>
  </section>
</main>
</body>
</html>
```